Business Cards Design for the electrical wholesaler: clean bold dynamic :)

We need a business card design that would follow our latest brand guidelines. As an electrical wholesaler we want to bring a fresh look and feel into the industry. The design should be clean bold and dynamic. It should come alive with the renewed energy of our green colour. Our grey colour should keep things balanced and complement the notion of maturity and responsibility. We employ Lato as a corporate font however are not bound by this font and we’re open to interpretation here.

Target Market(s)

Electrical contractors

Industry/Entity Type

Business

Contact Information for Business Card

Logo
Name & Surname: Halyna Dorosh
Job Title: Director of Marketing
Email: halya.dorosh@quillmail.example
Cell phone: XXX.XXX.XXXX
Address: 20517 - 87 Ave. Edmonton, AB, Canada. T6K 4N8
Business Phone: 780.555.0184
Website: www.brovix.example

Font styles to use
Other font styles liked:
• Lato

Requirements
Must have
• Logo & website
Nice to have
• Brand elements - some of them you may find in the attached Brand Guidelines (e.g. three lines on the background signifying "W")

```html
<!DOCTYPE html>
<html lang="en">
<head>
<meta charset="utf-8">
<title>brovix business cards</title>
<link rel="stylesheet" href="https://fonts.googleapis.com/css2?family=Work+Sans:wght@400;500&display=swap">
<style>
  :root {
    --green: #8dc63f;
    --grey: #58595b;
    --grey-dark: #4e4f51;
    --ink: #3d3d3f;
    --paper: #ffffff;
    --backdrop: #1e1e1e;
  }
  * { margin: 0; padding: 0; box-sizing: border-box; }
  html, body { width: 1200px; height: 897px; overflow: hidden; }
  body {
    position: relative;
    background: var(--backdrop);
    font-family: "Work Sans", sans-serif;
  }
  .card {
    position: absolute;
    left: 303px;
    width: 595px;
    height: 338px;
    border-radius: 24px;
    overflow: hidden;
  }
  .card--front { top: 92px; background: var(--paper); }
  .card--back { top: 469px; background: var(--grey); }

  .brand {
    position: absolute;
    display: flex;
    align-items: center;
    gap: 12px;
  }
  .brand__dot {
    width: 40px; height: 40px;
    border-radius: 50%;
    background: var(--green);
  }
  .brand__name {
    font-size: 58px;
    font-weight: 500;
    line-height: 1;
    letter-spacing: -1px;
  }
  .card--front .brand { left: 26px; top: 38px; }
  .card--front .brand__name { color: var(--ink); }
  .card--back .brand { left: 0; right: 0; top: 148px; justify-content: center; }
  .card--back .brand__name { color: var(--paper); }

  .contacts {
    position: absolute;
    left: 27px;
    top: 171px;
    list-style: none;
    font-size: 15px;
    color: var(--ink);
    letter-spacing: 0.4px;
  }
  .contacts li {
    display: flex;
    align-items: center;
    height: 19px;
  }
  .contacts svg { width: 10px; height: 10px; margin-right: 9px; flex: none; }
  .accent { color: var(--green); }

  .person {
    position: absolute;
    right: 26px;
    top: 170px;
    text-align: right;
  }
  .person__name {
    font-size: 24px;
    font-weight: 500;
    color: var(--green);
    letter-spacing: 0.3px;
  }
  .person__role {
    font-size: 15px;
    color: var(--ink);
    letter-spacing: 0.6px;
    margin-top: 2px;
  }

  .wave { position: absolute; left: 0; bottom: 0; width: 595px; height: 338px; }

  .address {
    position: absolute;
    right: 26px;
    top: 276px;
    text-align: right;
    font-size: 15px;
    line-height: 19px;
    color: var(--paper);
    letter-spacing: 0.8px;
  }

  .website {
    position: absolute;
    left: 0; right: 0;
    top: 297px;
    text-align: center;
    font-size: 15px;
    color: var(--paper);
    letter-spacing: 0.8px;
  }
</style>
</head>
<body>
  <section class="card card--front">
    <svg class="wave" viewBox="0 0 595 338" aria-hidden="true">
      <path d="M0,228 C60,290 150,318 260,292 C380,258 480,222 595,240 L595,338 L0,338 Z" fill="var(--green)"/>
      <path d="M0,272 C90,300 180,322 290,288 C390,256 480,240 595,300 L595,338 L0,338 Z" fill="var(--grey)"/>
    </svg>

    <div class="brand">
      <span class="brand__dot"></span>
      <span class="brand__name">brovix</span>
    </div>

    <ul class="contacts">
      <li>
        <svg viewBox="0 0 10 10"><path d="M2,0.5 L3.6,2.6 L2.8,3.8 C3.4,5.2 4.6,6.5 6.1,7.2 L7.3,6.4 L9.5,8 L8.4,9.5 C4.2,9 1,5.8 0.6,1.6 Z" fill="var(--green)"/></svg>
        780.555.0184
      </li>
      <li>
        <svg viewBox="0 0 10 10"><rect x="0.7" y="2" width="8.6" height="6" fill="none" stroke="var(--green)" stroke-width="1"/><path d="M0.7,2 L5,5.4 L9.3,2" fill="none" stroke="var(--green)" stroke-width="1"/></svg>
        halya.dorosh@quillmail.example
      </li>
      <li>
        <svg viewBox="0 0 10 10"><circle cx="5" cy="5" r="4.3" fill="none" stroke="var(--green)" stroke-width="0.9"/><ellipse cx="5" cy="5" rx="1.9" ry="4.3" fill="none" stroke="var(--green)" stroke-width="0.9"/><path d="M0.7,5 H9.3" stroke="var(--green)" stroke-width="0.9"/></svg>
        www.<span class="accent">brovix</span>.example
      </li>
    </ul>

    <div class="person">
      <p class="person__name">Halyna Dorosh</p>
      <p class="person__role">Founder</p>
    </div>

    <address class="address" style="font-style:normal">
      20517 87ave<br>
      T6K4N8 Edmonton, Alberta
    </address>
  </section>

  <section class="card card--back">
    <div class="brand">
      <span class="brand__dot"></span>
      <span class="brand__name">brovix</span>
    </div>
    <p class="website">www.<span class="accent">brovix</span>.example</p>
  </section>
</body>
</html>
```